professional business card design for technology company

We are a small technology consulting firm, specialising in consulting based around Cloud and Managed services. Our colour scheme is yellow, blue and white, as you can see in the logos. Although we are based in melbourne australia, due to the nature of our work, our clients can be located anywhere. We are looking for a clean, professional, positive look - similar to our company logo

Target Market(s)

small business

Industry/Entity Type

Business

Contact Information for Business Card

eye catching, designed to incorporate some level of raised printing. Must contain website address, phone number, name and job title

Requirements
Must have
• Logo (attached) - use of the same colour scheme

```html
<!DOCTYPE html>
<html lang="en">
<head>
<meta charset="utf-8">
<title>Nimbara Business Card</title>
<link rel="stylesheet" href="https://fonts.googleapis.com/css2?family=Raleway:wght@400;500;700;800&display=swap">
<style>
  :root {
    --bg: #e9e7e4;
    --card: #1a1a1a;
    --grey: #333333;
    --text-grey: #5c5c5c;
    --light: #d8d8d8;
    --blue: #27a7dc;
    --yellow: #f4d300;
  }
  * { margin: 0; padding: 0; box-sizing: border-box; }
  html, body { width: 1200px; height: 960px; overflow: hidden; }
  body { background: var(--bg); font-family: "Raleway", sans-serif; position: relative; }

  .card {
    position: absolute; left: 250px; width: 700px; height: 400px;
    background: var(--card); overflow: hidden;
    box-shadow: 0 6px 18px rgba(0,0,0,0.18);
  }
  .card--front { top: 52px; }
  .card--back { top: 508px; }

  .brand { display: flex; align-items: center; gap: 14px; position: absolute; }
  .brand__dot { width: 44px; height: 44px; border-radius: 50%; background: var(--blue); }
  .brand__name { font-weight: 800; color: var(--text-grey); letter-spacing: -1px; line-height: 1; }
  .card--front .brand { left: 50%; top: 50%; transform: translate(-50%, -50%); }
  .card--front .brand__name { font-size: 72px; }
  .card--back .brand { left: 150px; top: 48px; }
  .card--back .brand__dot { width: 36px; height: 36px; }
  .card--back .brand__name { font-size: 58px; }

  .card__shapes { position: absolute; inset: 0; }

  .ring {
    width: 30px; height: 30px; border: 2px solid var(--yellow); border-radius: 50%;
    display: flex; align-items: center; justify-content: center; flex: none;
  }
  .ring svg { width: 16px; height: 16px; fill: var(--light); }
  .ring--large { width: 40px; height: 40px; }
  .ring--large svg { width: 20px; height: 20px; }

  .person { position: absolute; left: 160px; top: 140px; display: flex; align-items: center; gap: 14px; }
  .person__name { font-size: 19px; font-weight: 700; color: var(--text-grey); text-transform: uppercase; letter-spacing: 0.5px; }
  .person__name span { color: var(--yellow); font-weight: 500; }
  .person__title { font-size: 13px; color: var(--light); margin-top: 2px; }

  .contacts { position: absolute; left: 150px; top: 218px; list-style: none; }
  .contacts li { display: flex; align-items: center; gap: 12px; margin-bottom: 10px; font-size: 14px; color: var(--light); letter-spacing: 0.3px; }
</style>
</head>
<body>

  <section class="card card--front">
    <div class="brand">
      <div class="brand__dot"></div>
      <div class="brand__name">Nimbara</div>
    </div>
  </section>

  <section class="card card--back">
    <svg class="card__shapes" viewBox="0 0 700 400" preserveAspectRatio="none">
      <rect width="700" height="400" fill="var(--grey)"/>
      <path d="M0 0 H600 Q592 240 500 400 H0 Z" fill="var(--blue)"/>
      <path d="M600 0 Q592 240 500 400" fill="none" stroke="#111" stroke-width="5"/>
      <path d="M596 225 Q575 330 500 400 H300 Z" fill="var(--yellow)"/>
      <path d="M0 0 H470 Q600 110 588 235 Q520 370 330 400 H0 Z" fill="var(--card)"/>
    </svg>

    <div class="brand">
      <div class="brand__dot"></div>
      <div class="brand__name">Nimbara</div>
    </div>

    <div class="person">
      <div class="ring ring--large">
        <svg viewBox="0 0 20 20"><circle cx="10" cy="6" r="4"/><path d="M2 19 Q2 11 10 11 Q18 11 18 19 Z"/></svg>
      </div>
      <div>
        <div class="person__name">Daniel <span>Hayes</span></div>
        <div class="person__title">Sales Director</div>
      </div>
    </div>

    <ul class="contacts">
      <li>
        <div class="ring"><svg viewBox="0 0 20 20"><path d="M2 5 H18 V15 H2 Z M2 5 L10 11 L18 5" fill="none" stroke="#d8d8d8" stroke-width="2"/></svg></div>
        hello@nimbara.com
      </li>
      <li>
        <div class="ring"><svg viewBox="0 0 20 20"><circle cx="10" cy="10" r="8" fill="none" stroke="#d8d8d8" stroke-width="2"/><path d="M2 10 H18 M10 2 Q5 10 10 18 M10 2 Q15 10 10 18" fill="none" stroke="#d8d8d8" stroke-width="1.5"/></svg></div>
        www.nimbara.com
      </li>
      <li>
        <div class="ring"><svg viewBox="0 0 20 20"><path d="M5 2 L8 2 L9 7 L7 8 Q8 12 12 13 L13 11 L18 12 L18 15 Q18 18 15 18 Q3 17 2 5 Q2 2 5 2 Z"/></svg></div>
        555-014-2287
      </li>
    </ul>
  </section>

</body>
</html>
```